KRV Business Card

Looking for a business card for my restaurant group I own. Four different concepts:

Copperfield Alehouse
Bristow Alehouse
Tanager's Stone Hearth Kitchen
Pellston Patty Company

Card doesn't need to include all the logos.

```html
<!DOCTYPE html>
<html lang="en">
<head>
<meta charset="utf-8">
<title>KRV Business Card</title>
<link rel="stylesheet" href="https://fonts.googleapis.com/css2?family=Lato:wght@400;700&family=Questrial&display=swap">
<style>
  :root {
    --backdrop: #2a2a2a;
    --card-white: #ffffff;
    --card-grey: #6d6e70;
    --gold: #c9a865;
    --ink: #4a4a4a;
    --rule: #d9d9d9;
  }
  html, body {
    margin: 0;
    width: 1200px;
    height: 1200px;
    overflow: hidden;
    background: var(--backdrop);
  }
  .stage { position: relative; width: 1200px; height: 1200px; }
  .card {
    position: absolute;
    top: 310px;
    width: 364px;
    height: 594px;
    box-shadow: 0 2px 6px rgba(0,0,0,0.45);
    text-align: center;
    box-sizing: border-box;
  }
  .card--front { left: 234px; background: var(--card-white); }
  .card--back { left: 628px; width: 368px; background: var(--card-grey); }

  .brand-initials {
    position: absolute; left: 0; right: 0; top: 86px;
    font-family: "Questrial", sans-serif;
    font-size: 72px; letter-spacing: 4px; line-height: 1;
    color: var(--gold);
  }
  .brand-name {
    position: absolute; left: 0; right: 0; top: 176px;
    font-family: "Questrial", sans-serif;
    font-size: 19px; letter-spacing: 3px; line-height: 1.35;
    color: var(--gold);
    text-transform: uppercase;
  }
  .holder-name {
    position: absolute; left: 0; right: 0; top: 334px;
    font-family: "Questrial", sans-serif;
    font-size: 24px; letter-spacing: 0.5px;
    color: var(--gold);
    text-transform: uppercase;
  }
  .holder-role {
    position: absolute; left: 0; right: 0; top: 360px;
    font-family: "Lato", sans-serif; font-size: 17px;
    color: var(--ink);
  }
  .contact-divider { position: absolute; left: 86px; top: 395px; }
  .contact-list {
    position: absolute; left: 0; right: 0; top: 430px;
    font-family: "Lato", sans-serif; font-size: 17px; line-height: 22px;
    color: var(--ink);
  }
  .contact-rule {
    position: absolute; left: 90px; right: 82px; top: 506px;
    height: 1px; background: var(--rule);
  }
  .address {
    position: absolute; left: 0; right: 0; top: 517px;
    font-family: "Lato", sans-serif; font-size: 17px; line-height: 22px;
    color: var(--ink);
  }

  .back-initials {
    position: absolute; left: 0; right: 0; top: 214px;
    font-family: "Questrial", sans-serif;
    font-size: 96px; letter-spacing: 6px; line-height: 1;
    color: var(--gold);
  }
  .concept-list {
    position: absolute; left: 0; right: 0; top: 459px;
    margin: 0; padding: 0; list-style: none;
    font-family: "Lato", sans-serif; font-weight: 700;
    font-size: 15px; line-height: 22.5px;
    color: var(--card-white);
    text-transform: uppercase;
  }
</style>
</head>
<body>
<main class="stage">
  <section class="card card--front">
    <div class="brand-initials">KRV</div>
    <div class="brand-name">Kingsreach<br>Hospitality Group</div>

    <div class="holder-name">Daniel Harrow</div>
    <div class="holder-role">Managing Director</div>

    <svg class="contact-divider" width="192" height="26" viewBox="0 0 192 26" aria-hidden="true">
      <line x1="0" y1="13" x2="52" y2="13" stroke="#8a8a8a" stroke-width="1"/>
      <line x1="140" y1="13" x2="192" y2="13" stroke="#8a8a8a" stroke-width="1"/>
      <circle cx="67" cy="13" r="12" fill="#c9a865"/>
      <path d="M61 16c0-4 3-7 6-7s6 3 6 7z M64 9h6v-2h-6z" fill="#fff"/>
      <circle cx="95" cy="13" r="12" fill="#c9a865"/>
      <rect x="88" y="8" width="14" height="10" fill="none" stroke="#fff" stroke-width="1.5"/>
      <path d="M88 8l7 6 7-6" fill="none" stroke="#fff" stroke-width="1.5"/>
      <circle cx="123" cy="13" r="12" fill="#c9a865"/>
      <circle cx="123" cy="13" r="7" fill="none" stroke="#fff" stroke-width="1.5"/>
      <path d="M116 13h14 M123 6c-3 4-3 10 0 14 M123 6c3 4 3 10 0 14" fill="none" stroke="#fff" stroke-width="1.2"/>
    </svg>

    <div class="contact-list">
      044-987 654 321<br>
      hello@kingsreach.com<br>
      www.kingsreach.com
    </div>
    <div class="contact-rule"></div>
    <div class="address">318, Orchard Lane West,<br>60214, Calderia</div>
  </section>

  <section class="card card--back">
    <div class="back-initials">KRV</div>
    <ul class="concept-list">
      <li>Copperfield Alehouse</li>
      <li>Bristow Alehouse</li>
      <li>Tanager's Stone Hearth Kitchen</li>
      <li>Pellston Patty Company</li>
    </ul>
  </section>
</main>
</body>
</html>
```